Redesign of business card for Cedar Ridge Mechanical

We are looking for a new design for our business cards for Cedar Ridge Mechanical. We are a plumbing & HVAC construction company, operating on the West Coast of Canada and USA. Logo attached.
Industry/Entity Type
Construction - Plumbing & HVAC
Contact Information for Business Card
Name, address, phone numbers, email, website address
Look and feel
Each slider illustrates characteristics of the customer's brand and the style your logo design should communicate.

```html
<!DOCTYPE html>
<html lang="en">
<head>
<meta charset="utf-8">
<title>Cedar Ridge Mechanical – Business Card</title>
<link rel="stylesheet" href="https://fonts.googleapis.com/css2?family=Montserrat:wght@400;500;700&display=swap">
<style>
  :root {
    --stage: #1c1c1c;
    --card-light: #ffffff;
    --card-dark: #262626;
    --ink: #1a1a1a;
    --ink-soft: #2a2a2a;
    --paper-text: #ffffff;
  }
  * { box-sizing: border-box; margin: 0; padding: 0; }
  html, body {
    width: 1200px; height: 1200px; overflow: hidden;
    background: var(--stage);
    font-family: "Montserrat", Arial, sans-serif;
  }
  .card {
    position: absolute;
    left: 233px;
    width: 682px;
    height: 406px;
    border-radius: 26px;
  }
  .card-front { top: 217px; background: var(--card-light); color: var(--ink); }
  .card-back { top: 694px; background: var(--card-dark); color: var(--paper-text); }

  .holder { position: absolute; left: 32px; top: 43px; }
  .holder-name { font-size: 24px; font-weight: 700; letter-spacing: 0.2px; line-height: 1.2; }
  .holder-title { font-size: 15px; font-weight: 500; margin-top: 3px; }

  .brand-front {
    position: absolute; right: 50px; top: 38px;
    display: flex; align-items: center; gap: 10px;
    font-size: 15px; font-weight: 700; color: var(--ink);
    text-transform: uppercase; letter-spacing: 0.5px;
  }
  .brand-mark { width: 22px; height: 22px; background: currentColor; }

  .contact-list { position: absolute; left: 32px; top: 278px; list-style: none; }
  .contact-item {
    display: flex; align-items: center; gap: 12px;
    font-size: 15px; font-weight: 500; height: 28.5px; color: var(--ink-soft);
  }
  .contact-icon { width: 14px; height: 14px; fill: var(--ink); }

  .address {
    position: absolute; right: 50px; top: 322px;
    text-align: right; font-size: 15px; font-weight: 500; line-height: 18px;
    font-style: normal; color: var(--ink-soft);
  }

  .brand-back {
    position: absolute; left: 0; right: 0; top: 0; bottom: 0;
    display: flex; align-items: center; justify-content: center; gap: 18px;
    font-size: 32px; font-weight: 700; text-transform: uppercase; letter-spacing: 1px;
  }
  .brand-back .brand-mark { width: 36px; height: 36px; }
</style>
</head>
<body>
  <section class="card card-front" aria-label="Business card front">
    <div class="holder">
      <p class="holder-name">Daniel Marsh</p>
      <p class="holder-title">Managing Director</p>
    </div>

    <div class="brand-front"><span class="brand-mark"></span><span>Cedar Ridge Mechanical</span></div>

    <ul class="contact-list">
      <li class="contact-item">
        <svg class="contact-icon" viewBox="0 0 24 24" aria-hidden="true"><path d="M6.6 10.8c1.4 2.8 3.8 5.1 6.6 6.6l2.2-2.2c.3-.3.7-.4 1-.2 1.1.4 2.3.6 3.6.6.6 0 1 .4 1 1V20c0 .6-.4 1-1 1C10.6 21 3 13.4 3 4c0-.6.4-1 1-1h3.5c.6 0 1 .4 1 1 0 1.3.2 2.5.6 3.6.1.3 0 .7-.2 1l-2.3 2.2z"/></svg>
        <span>888.555.0142</span>
      </li>
      <li class="contact-item">
        <svg class="contact-icon" viewBox="0 0 24 24" aria-hidden="true"><path d="M2 5h20v2l-10 6L2 7z"/><path d="M2 9l10 6 10-6v10H2z"/></svg>
        <span>info@cedarridgemechanical.com</span>
      </li>
      <li class="contact-item">
        <svg class="contact-icon" viewBox="0 0 24 24" aria-hidden="true"><circle cx="12" cy="12" r="9" fill="none" stroke="#1a1a1a" stroke-width="2.4"/><path d="M3 12h18M12 3c3 3 3 15 0 18M12 3c-3 3-3 15 0 18" fill="none" stroke="#1a1a1a" stroke-width="2"/></svg>
        <span>www.cedarridgemechanical.com</span>
      </li>
    </ul>

    <address class="address">248 Fern Hollow Drive<br>Salem, OR 97301</address>
  </section>

  <section class="card card-back" aria-label="Business card back">
    <div class="brand-back"><span class="brand-mark"></span><span>Cedar Ridge Mechanical</span></div>
  </section>
</body>
</html>
```